Design a Website for an IT Support Company

We are an IT support company that provides commercial IT support and services to small and medium sized businesses. We are in need of a website to be developed for our business.
We would like to work with someone who is either familiar with the IT field, or has developed a website for an IT support company in the past.
Some examples of designs/layouts that we like:
https://www.veldaworks.example/
http://www.marsbyquill.example/
http://817kq.example/
http://www.olbenstructures.example/
http://www.bykq.example/
I have attached a word document that gives a menu system/page layout format that we would like for our website as well as branch office phone numbers. Our logo is also attached that you can use for your design purposes. We currently do not have copy produced for all of the pages outlined in the word document, but would get this done during the project with the selected designer.
We would like the website to be SEO friendly & fully responsive. We would prefer a Wordpress format, however, we are open to HTML formats as well.

```html
<!DOCTYPE html>
<html lang="en">
<head>
<meta charset="utf-8">
<title>Tempra IT – Commercial IT Support</title>
<link rel="stylesheet" href="https://fonts.googleapis.com/css2?family=Roboto+Condensed:wght@400;700&family=Open+Sans:ital,wght@0,400;0,600;0,700;1,400&display=swap">
<style>
:root{
  --blue:#1b6fba;
  --blue-dark:#155c9c;
  --green:#23a94b;
  --ink:#333;
  --muted:#666;
  --hero-a:#0d1014;
  --hero-b:#3a4048;
  --why-bg:#a6b6bf;
  --blog-bg:#efefef;
  --footer:#1f1f1f;
  --footer-base:#161616;
  --white:#fff;
}
*{box-sizing:border-box;margin:0;padding:0}
html,body{width:1200px;height:3186px;overflow:hidden}
body{position:relative;background:var(--white);font-family:"Open Sans",Arial,sans-serif;color:var(--ink)}
.abs{position:absolute}
.heading{font-family:"Roboto Condensed",Arial Narrow,sans-serif}

/* hero */
.hero{left:0;top:0;width:1200px;height:660px;background:linear-gradient(100deg,var(--hero-a) 0%,#1a1e24 45%,var(--hero-b) 100%)}
.hero-edge{left:0;top:560px;width:1200px;height:110px}
.brand{left:100px;top:34px;display:flex;align-items:center;gap:12px;color:var(--white);font-size:34px;font-weight:600}
.brand-dot{width:34px;height:34px;border-radius:50%;background:var(--white)}
.topbar{top:38px;right:100px;display:flex;gap:28px;font-size:14px;color:var(--white)}
.topbar span{display:flex;align-items:center;gap:9px}
.topbar .ico{width:22px;height:22px;border-radius:50%;background:var(--blue);display:flex;align-items:center;justify-content:center}
.nav{top:85px;left:574px;display:flex;align-items:center;gap:0;font-size:13px;color:var(--white);font-weight:600}
.nav a{color:var(--white);text-decoration:none;padding:7px 18px;border:2px solid transparent;border-radius:20px;margin-right:0}
.nav a.active{border-color:var(--white)}
.hero-title{left:98px;top:236px;color:var(--white);font-size:42px;font-weight:700;line-height:44px;text-transform:uppercase}
.hero-text{left:100px;top:340px;width:400px;color:#ddd;font-size:13px;line-height:21px}
.btn{display:inline-flex;align-items:center;gap:8px;font-size:12px;font-weight:600;text-transform:uppercase;color:var(--white);text-decoration:none}
.hero-btn{left:100px;top:431px;height:32px;padding:0 16px;border:2px solid var(--blue);border-radius:18px;background:var(--blue-dark)}
.dots{left:573px;top:598px;display:flex;gap:8px}
.dots i{width:13px;height:13px;border-radius:50%;border:1.5px solid #555;display:block}
.dots i.on{background:#fff;border-color:#fff}

/* sections */
.sec-title{width:1200px;left:0;text-align:center;font-size:36px;color:#333;font-weight:400}
.rule{left:570px;width:60px;height:3px;background:var(--blue)}

.card{top:877px;width:314px;height:338px;color:var(--white);border-radius:2px}
.card.blue{background:var(--blue)}
.card.green{background:var(--green)}
.card-badge{left:99px;top:-61px;width:116px;height:116px;border-radius:50%;background:var(--white);border:7px solid var(--blue);display:flex;align-items:center;justify-content:center}
.green .card-badge{border-color:var(--green)}
.card h3{position:absolute;top:68px;width:100%;text-align:center;font-family:"Roboto Condensed",sans-serif;font-weight:400;font-size:21px}
.card ul{position:absolute;left:26px;top:134px;list-style:none;font-size:12.5px;line-height:28.6px}
.card li::before{content:"";display:inline-block;width:7px;height:7px;border-radius:50%;background:var(--white);margin-right:16px;vertical-align:1px}
.card .more{position:absolute;left:26px;top:290px;height:26px;padding:0 10px;border:1.5px solid var(--white);border-radius:14px;font-size:10px}

.why{left:0;top:1310px;width:1200px;height:450px;background:var(--why-bg)}
.why-photo{left:0;top:0;width:640px;height:450px;background:linear-gradient(90deg,#d8dde0 0%,#c3ced4 60%,var(--why-bg) 100%)}
.why h2{position:absolute;left:620px;top:88px;color:var(--white);font-size:34px;font-weight:700}
.why p{position:absolute;left:621px;width:470px;color:#f3f5f6;font-size:11.5px;line-height:19px}
.why .btn{position:absolute;left:621px;top:334px;height:30px;padding:0 18px;background:var(--blue)}

.bubble{left:505px;top:1832px}
.quote{left:170px;top:2000px;width:860px;text-align:center;font-style:italic;color:#666;font-size:12.5px;line-height:22px}
.quote q{quotes:"\201C" "\201D"}
.who{top:2098px;left:0;width:1200px;text-align:center;font-size:15px;color:#555}
.who b{font-style:italic;color:#333}
.bars{left:548px;top:2150px;display:flex;gap:6px}
.bars i{display:block;width:32px;height:4px;background:#a9cbe8}
.bars i.on{background:var(--blue)}

.blog{left:0;top:2234px;width:1200px;height:570px;background:var(--blog-bg)}
.post{top:181px;width:314px;height:310px;background:var(--white)}
.post-img{height:176px}
.post h4{margin:24px 16px 0;font-size:14px;font-weight:400;color:#444}
.post .meta{margin:10px 16px 0;font-size:12px;color:#666}
.post p{margin:10px 16px 0;font-size:11.5px;line-height:21px;color:#555}

.footer{left:0;top:2804px;width:1200px;height:312px;background:var(--footer);color:#ddd}
.footer-base{left:0;top:3116px;width:1200px;height:70px;background:var(--footer-base);color:#ccc;font-size:12px;text-align:center;line-height:70px}
.footer h5{position:absolute;top:52px;font-family:"Roboto Condensed",sans-serif;font-weight:400;font-size:17px;color:var(--white);text-transform:uppercase}
.f-brand{position:absolute;left:100px;top:110px;display:flex;align-items:center;gap:10px;color:var(--white);font-size:30px;font-weight:600}
.social{position:absolute;left:100px;top:170px;display:flex;gap:5px}
.social i{display:block;width:20px;height:20px;border-radius:50%;border:1.5px solid #bbb}
.f-contact{position:absolute;left:374px;top:96px;font-size:12px;line-height:20px}
.f-contact .row{display:flex;gap:18px;margin-bottom:14px}
.f-links{position:absolute;left:665px;top:98px;list-style:none;font-size:12px;line-height:25.5px}
.f-links li::before{content:"";display:inline-block;width:9px;height:9px;border-radius:50%;background:#ddd;margin-right:12px;vertical-align:0}
.f-news p{position:absolute;left:856px;top:96px;width:250px;font-size:11.5px;line-height:20px}
.f-input{position:absolute;left:856px;top:140px;width:244px;height:42px;background:var(--white);color:#666;font-size:11px;line-height:42px;padding-left:12px}
.f-btn{position:absolute;left:856px;top:195px;height:32px;padding:0 14px;background:var(--blue);color:var(--white);font-size:12px;line-height:32px}
</style>
</head>
<body>

<header class="hero abs" role="img" aria-label="Photo of a businessman holding a tablet with a glowing cloud and network icons">
</header>
<svg class="hero-edge abs" viewBox="0 0 1200 110" preserveAspectRatio="none" aria-hidden="true">
  <path d="M0 16 Q600 80 1200 86 L1200 110 L0 110 Z" fill="#fff"/>
  <path d="M0 16 Q600 80 1200 86" fill="none" stroke="#1b6fba" stroke-width="4"/>
</svg>

<div class="brand abs"><span class="brand-dot"></span>Tempra IT</div>

<div class="topbar abs">
  <span><i class="ico"><svg width="11" height="11" viewBox="0 0 24 24"><path fill="#fff" d="M6.6 10.8a15 15 0 006.6 6.6l2.2-2.2c.3-.3.7-.4 1-.2 1.1.4 2.3.6 3.6.6.6 0 1 .4 1 1V20c0 .6-.4 1-1 1A17 17 0 013 4c0-.6.4-1 1-1h3.5c.6 0 1 .4 1 1 0 1.3.2 2.5.6 3.6.1.3 0 .7-.2 1z"/></svg></i>555-014-2200</span>
  <span><i class="ico"><svg width="11" height="11" viewBox="0 0 24 24"><path fill="#fff" d="M2 5h20v14H2z"/><path d="M2 5l10 8 10-8" fill="none" stroke="#1b6fba" stroke-width="2"/></svg></i>hello@tempra-it.example</span>
</div>

<nav class="nav abs">
  <a class="active" href="#">HOME</a><a href="#">OUR SERVICES</a><a href="#">WHY TEMPRA IT</a><a href="#">BLOG</a><a href="#">CONTACT</a>
</nav>

<h1 class="hero-title heading abs">Tempra Commercial<br>IT Support</h1>
<p class="hero-text abs">Sed ut perspiciatis unde omnis iste natus error sit voluptatem accusantium doloremque laudantium, totam rem aperiam, eaque ipsa quae</p>
<a class="btn hero-btn abs" href="#">Read more <svg width="12" height="12" viewBox="0 0 12 12"><circle cx="6" cy="6" r="6" fill="#fff"/><path d="M5 3.5 7.5 6 5 8.5" fill="none" stroke="#155c9c" stroke-width="1.6"/></svg></a>
<div class="dots abs"><i class="on"></i><i></i><i></i></div>

<!-- services -->
<h2 class="sec-title heading abs" style="top:712px">IT SUPPORT &amp; SERVICES</h2>
<div class="rule abs" style="top:771px"></div>

<section class="card blue abs" style="left:100px">
  <div class="card-badge abs"><svg width="52" height="52" viewBox="0 0 52 52" fill="none" stroke="#333" stroke-width="2.2"><rect x="19" y="19" width="14" height="14"/><circle cx="8" cy="8" r="4"/><circle cx="44" cy="8" r="4"/><circle cx="8" cy="44" r="4"/><circle cx="44" cy="44" r="4"/><circle cx="26" cy="5" r="3"/><circle cx="26" cy="47" r="3"/><path d="M11 11l8 8M41 11l-8 8M11 41l8-8M41 41l-8-8M26 8v11M26 33v11"/></svg></div>
  <h3>DATA SERVICES</h3>
  <ul><li>Managed IT Services</li><li>IT Support &amp; Consulting</li><li>IT Helpdesk Services</li><li>Network Security</li><li>Data Backup &amp; Recovery</li></ul>
  <a class="btn more" href="#">Read more</a>
</section>

<section class="card green abs" style="left:443px">
  <div class="card-badge abs"><svg width="54" height="52" viewBox="0 0 54 52" fill="none" stroke="#333" stroke-width="2.2"><path d="M15 22a8 8 0 010-16 11 11 0 0121-2 8 8 0 014 15H15z"/><path d="M27 22v8M27 30h-16v4M27 30h16v4"/><rect x="4" y="34" width="14" height="12"/><rect x="36" y="34" width="14" height="12"/><rect x="21" y="34" width="12" height="14"/></svg></div>
  <h3>CLOUD SERVICES</h3>
  <ul><li>Cloud Mail Migrations</li><li>Public Cloud Management Services</li><li>Cloud Migration Services</li><li>Hosted Virtual Servers</li><li>Hosted Telephone Systems</li></ul>
  <a class="btn more" href="#">Read more</a>
</section>

<section class="card blue abs" style="left:786px">
  <div class="card-badge abs"><svg width="50" height="44" viewBox="0 0 50 44" fill="#333"><path d="M4 15h10l20-12v36L14 27H4z"/><path d="M10 27h8l4 14h-7z"/><path d="M40 14q5 7 0 14" fill="none" stroke="#333" stroke-width="3"/></svg></div>
  <h3>VOICE SERVICES</h3>
  <ul><li>Open PBX Consulting</li><li>Business Telephone Systems</li><li>Multiple Office Phone Systems</li><li>Desk Handset Systems</li><li>SIP Trunks</li></ul>
  <a class="btn more" href="#">Read more</a>
</section>

<!-- why -->
<section class="why abs">
  <div class="why-photo abs" role="img" aria-label="Photo of a smiling man in a blue shirt working on a laptop in an office"></div>
  <h2 class="heading">WHY TEMPRA IT</h2>
  <p style="top:154px">Sed ut perspiciatis unde omnis iste natus error sit voluptatem accusantium doloremque laudantium, totam rem aperiam, eaque ipsa quae ab illo inventore veritatis et quasi architecto beatae vitae dicta sunt explicabo. Nemo enim ipsam voluptatem quia voluptas sit aspernatur aut odit aut fugit, sed quia consequuntur magni dolores eos.</p>
  <p style="top:246px">Totam rem aperiam, eaque ipsa quae ab illo inventore veritatis et quasi architecto beatae vitae dicta sunt explicabo. Nemo enim ipsam voluptatem quia voluptas sit aspernatur aut odit aut fugit, sed quia consequuntur magni dolores eos.</p>
  <a class="btn" href="#">Read more</a>
</section>

<!-- testimonial -->
<svg class="bubble abs" width="190" height="140" viewBox="0 0 190 140">
  <path d="M40 112 L20 138 L66 120" fill="#fff" stroke="#999" stroke-width="8" stroke-linejoin="round"/>
  <ellipse cx="98" cy="64" rx="86" ry="58" fill="#fff" stroke="#999" stroke-width="8"/>
  <circle cx="96" cy="64" r="46" fill="#c9a58e" role="img" aria-label="Portrait of the reviewer"/>
</svg>
<p class="quote abs"><q>Lorem ipsum dolor sit amet, consectetur adipiscing elit, sed do eiusmod tempor incididunt ut labore et dolore magna aliqua. Ut enim ad minim veniam, quis nostrud exercitation ullamco laboris nisi ut aliquip ex ea commodo consequat. Duis aute irure dolor in reprehenderit in voluptate velit esse cillum dolore eu fugiat nulla pariatur. Excepteur sint occaecat</q></p>
<p class="who abs"><b>John Doe</b> - Manager</p>
<div class="bars abs"><i class="on"></i><i></i><i></i></div>

<!-- blog -->
<section class="blog abs">
  <h2 class="sec-title heading abs" style="top:80px">LATEST BLOG</h2>
  <div class="rule abs" style="top:136px"></div>

  <article class="post abs" style="left:100px">
    <div class="post-img" role="img" aria-label="Photo of a hand touching a glowing cloud network graphic" style="background:linear-gradient(135deg,#1d3f63,#5b86ad)"></div>
    <h4>Nemo enim ipsam voluptatem</h4>
    <p class="meta">&#9719; 3 minutes ago, 0 comments</p>
    <p>Lorem ipsum dolor sit amet, consectetur adipiscing elit, sed do eiusmod tempor incididunt</p>
  </article>
  <article class="post abs" style="left:443px">
    <div class="post-img" role="img" aria-label="Photo of hands typing on a laptop keyboard" style="background:linear-gradient(135deg,#e4d9c6,#8a8784)"></div>
    <h4>Nemo enim ipsam voluptatem</h4>
    <p class="meta">&#9719; 3 minutes ago, 0 comments</p>
    <p>Lorem ipsum dolor sit amet, consectetur adipiscing elit, sed do eiusmod tempor incididunt</p>
  </article>
  <article class="post abs" style="left:786px">
    <div class="post-img" role="img" aria-label="Photo of a person in a dark server control room with screens" style="background:linear-gradient(135deg,#0f1620,#3c4a5c)"></div>
    <h4>Nemo enim ipsam voluptatem</h4>
    <p class="meta">&#9719; 3 minutes ago, 0 comments</p>
    <p>Lorem ipsum dolor sit amet, consectetur adipiscing elit, sed do eiusmod tempor incididunt</p>
  </article>
</section>

<!-- footer -->
<footer class="footer abs">
  <div class="f-brand"><span class="brand-dot" style="width:28px;height:28px"></span>Tempra IT</div>
  <div class="social"><i></i><i></i><i></i><i></i><i></i></div>

  <h5 style="left:374px">Contact Us</h5>
  <div class="f-contact">
    <div class="row"><svg width="14" height="20" viewBox="0 0 14 20"><path fill="#ddd" d="M7 0a7 7 0 00-7 7c0 5 7 13 7 13s7-8 7-13a7 7 0 00-7-7zm0 10a3 3 0 110-6 3 3 0 010 6z"/></svg><span>48 Tempra - Larkfield Road<br>next to the Civic Hall</span></div>
    <div class="row"><svg width="16" height="16" viewBox="0 0 24 24"><path fill="none" stroke="#ddd" stroke-width="2" d="M6.6 10.8a15 15 0 006.6 6.6l2.2-2.2c.3-.3.7-.4 1-.2 1.1.4 2.3.6 3.6.6.6 0 1 .4 1 1V20c0 .6-.4 1-1 1A17 17 0 013 4c0-.6.4-1 1-1h3.5c.6 0 1 .4 1 1 0 1.3.2 2.5.6 3.6.1.3 0 .7-.2 1z"/></svg><span>Main Number: 555-014-2200<br>Houston: 555-017-3300<br>San Antonio: 555-019-4400<br>Austin: 555-012-5500<br>Tulsa: 555-016-6600<br>Oklahoma City: 555-018-7700</span></div>
  </div>

  <h5 style="left:665px">Quick Links</h5>
  <ul class="f-links"><li>Home</li><li>About Us</li><li>Services</li><li>Why Tempra IT</li><li>Blog</li><li>Contact Us</li></ul>

  <h5 style="left:856px">Sign up for newsletter</h5>
  <div class="f-news"><p>Excepteur sint occaecat cupidatat non proident, sunt in culpa qui officia deserunt</p></div>
  <div class="f-input">Enter email</div>
  <div class="f-btn">SUBSCRIPTION</div>
</footer>
<div class="footer-base abs">©2017 Tempra. All Rights Reserved.</div>

</body>
</html>
```